Wilderness Doc & TV personality personal page

I’m a wilderness and EMS emergency physician with particular sub specialties and a TV show. I need a website to highlight my interviews, teachings, etc... I did buy a number of domains for now.
Topics and things I need: CV (or version) me in the media, picture gallery, actually I sort of really like what dr owen barkley, my colleague has setup plus I have tv show and stuff like that. ridgeway healer dot com

Target Market(s)

EMS, education, commercial products...

Industry/Entity Type

Medical And Science

Coding

Coded - Design and coding required

Number of Pages Required

1 page

Font styles to use
Sans Serif

Colors
f37122
9bcb3c
0556a4
a54499

Requirements
Must have
• Links and photos to news articles and things that mention me that I can add in.
Nice to have
• Maybe some snapshots of lecture reviews or patient thank you notes. Accolades so to speak
• I really appreciate how sharp it is. I would love to see Headings that resemble my friend's at ridgeway healer dot com. Home, experience, consulting, lectures, affiliates, contact... those are main subjects... I think media also and that will have the TV show stuff and articles written about me...then maybe at the bottom of main page also have splits for training, research, television, and maybe exploration
Should not have
• The medical symbol with two snakes... that means quack doctor

```html
<!DOCTYPE html>
<html lang="en">
<head>
<meta charset="utf-8">
<title>Reid Calloway — Wilderness &amp; EMS</title>
<link href="https://fonts.googleapis.com/css2?family=Montserrat:wght@400;500;600;700;800&family=Poppins:wght@400;500;600&display=swap" rel="stylesheet">
<style>
:root{
  --orange:#f37122;
  --green:#9bcb3c;
  --blue:#0556a4;
  --purple:#a54499;
  --ink:#0d0d0d;
  --bar:#141414;
  --white:#ffffff;
  --muted:#cfcfcf;
  --line:#d9d9d9;
}
*{box-sizing:border-box;margin:0;padding:0}
html,body{width:1200px;height:3779px;overflow:hidden;background:var(--ink)}
body{position:relative;font-family:"Poppins",sans-serif;color:var(--white)}
.abs{position:absolute}
.photo{position:absolute;border:1px solid var(--orange);border-radius:3px}
h2.section-title{position:absolute;left:0;width:1200px;text-align:center;font-family:"Montserrat",sans-serif;font-weight:700;font-size:32px;letter-spacing:0.5px}
.round-arrow{position:absolute;width:40px;height:40px}

/* header */
.site-header{left:0;top:0;width:1200px;height:94px;background:var(--bar);border-bottom:1px solid #2a2a2a}
.brand{left:140px;top:40px;font-family:"Montserrat",sans-serif;white-space:nowrap}
.brand .name{font-size:22px;font-weight:800;color:var(--orange);line-height:1}
.brand .tag{font-size:12px;font-weight:600;color:var(--white);margin-top:3px}
.contact-line{top:12px;right:108px;display:flex;gap:28px;font-family:"Montserrat",sans-serif;font-weight:700;font-size:17px;align-items:center;white-space:nowrap}
.contact-line span{display:flex;align-items:center;gap:8px}
.main-nav{top:58px;left:384px;display:flex;gap:34px;font-family:"Montserrat",sans-serif;font-weight:600;font-size:16px;white-space:nowrap}
.main-nav a{color:var(--white);text-decoration:none;position:relative}
.main-nav a.active{color:var(--orange)}
.main-nav a.active::after{content:"";position:absolute;left:50%;top:28px;margin-left:-7px;border:7px solid transparent;border-bottom-color:var(--orange)}

/* hero */
.hero{left:0;top:94px;width:1200px;height:613px;background:radial-gradient(circle at 75% 20%,#2f7fd6 0%,#1a5fb8 40%,#0c3c7c 100%)}
.hero-portrait{left:0;top:0;width:630px;height:613px;background:linear-gradient(180deg,rgba(240,240,240,.0) 0%,rgba(236,238,242,.85) 45%,#e9ecf0 100%);}
.hero-title{left:646px;top:138px;font-family:"Montserrat",sans-serif;font-weight:800;font-size:54px;line-height:1;letter-spacing:0.5px;white-space:nowrap}
.hero-sub{left:648px;top:212px;width:450px;font-family:"Montserrat",sans-serif;font-weight:600;font-size:21px;line-height:1.4;color:#e6eef8}
.btn-outline{left:648px;top:290px;width:152px;height:54px;border:2px solid var(--white);display:flex;align-items:center;justify-content:center;font-family:"Montserrat",sans-serif;font-weight:700;font-size:15px}
.play-video{left:818px;top:288px;display:flex;align-items:center;gap:12px;font-family:"Montserrat",sans-serif;font-weight:700;font-size:16px;line-height:1.3}
.hero-strip{left:648px;top:364px;width:440px;height:114px;background:rgba(10,30,70,.55);padding:8px;display:flex;gap:8px}
.hero-strip div{flex:1;border:2px solid var(--white)}

/* media */
.media-sub{left:0;top:830px;width:1200px;text-align:center;font-size:13px;font-weight:500}
.ep-bar{position:absolute;left:0;right:0;bottom:0;height:34px;background:var(--blue);display:flex;justify-content:space-between;align-items:center;padding:0 10px;font-family:"Montserrat",sans-serif;font-size:12px;font-weight:700;line-height:1.1}
.ep-bar em{font-style:normal;font-weight:400}

/* about */
.about{left:112px;top:1402px;width:976px;height:350px;border:2px solid var(--line)}
.about h3{position:absolute;left:28px;top:36px;font-family:"Montserrat",sans-serif;font-weight:700;font-size:33px}
.about p{position:absolute;left:30px;top:88px;width:516px;font-size:13px;line-height:28px;text-align:justify}
.btn-cv{left:30px;top:260px;height:42px;padding:0 18px;background:var(--blue);border-radius:3px;display:flex;align-items:center;gap:8px;font-family:"Montserrat",sans-serif;font-weight:700;font-size:15px}

/* gallery */
.g-tile{position:absolute}

/* consulting */
.c-bar{position:absolute;left:0;right:0;bottom:0;height:46px;display:flex;justify-content:space-between;align-items:center;padding:0 14px 0 16px;font-family:"Montserrat",sans-serif;font-weight:700;font-size:19px}

/* affiliates */
.affiliates{left:112px;top:2970px;width:976px;display:flex;justify-content:space-between;align-items:center;font-family:"Montserrat",sans-serif;font-weight:700;font-size:25px}
.affiliates span{display:flex;align-items:center;gap:10px}
.affiliates i{display:inline-block;width:24px;height:24px;background:var(--white);border-radius:50%}

/* contact */
.contact{left:112px;top:3106px;width:976px;height:365px;border:2px solid var(--line);background:linear-gradient(180deg,#3a3f63 0%,#2c2f52 55%,#23264a 100%)}
.contact-photo{left:460px;top:0;width:300px;height:361px;background:linear-gradient(180deg,#4b4e72 0%,#2e3b6a 100%);opacity:.8}
.contact h3{position:absolute;left:144px;top:48px;font-family:"Montserrat",sans-serif;font-weight:700;font-size:34px}
.contact .lead{position:absolute;left:146px;top:98px;font-size:13px;font-weight:600}
.field{position:absolute;height:50px;background:rgba(255,255,255,.72);border-radius:2px;color:#555;font-size:13px;padding:16px 18px}
.submit{position:absolute;left:492px;top:264px;width:344px;height:50px;background:var(--blue);display:flex;align-items:center;justify-content:center;gap:8px;font-family:"Montserrat",sans-serif;font-weight:600;font-size:16px}

/* footer */
.footer-brand{left:150px;top:3566px;font-family:"Montserrat",sans-serif;white-space:nowrap}
.footer-brand .name{font-size:26px;font-weight:800;color:var(--orange);line-height:1}
.footer-brand .tag{font-size:15px;font-weight:600;margin-top:3px}
.socials{left:126px;top:3636px;display:flex;gap:10px}
.socials i{width:32px;height:32px;border:2px solid var(--white);border-radius:50%;display:block}
.f-col{top:3524px;font-size:13.5px;line-height:28.5px;white-space:nowrap}
.f-col h4{font-family:"Montserrat",sans-serif;font-weight:600;font-size:14px;margin-bottom:12px}
.f-col .dir{color:var(--orange)}
.footer-rule{left:0;top:3719px;width:1200px;height:1px;background:#333}
.copyright{left:0;top:3741px;width:1200px;text-align:center;font-size:13px}
</style>
</head>
<body>

<header class="abs site-header">
  <div class="abs brand"><div class="name">REID CALLOWAY</div><div class="tag">wilderness &amp; EMS</div></div>
  <div class="abs contact-line">
    <span><svg width="30" height="30" viewBox="0 0 30 30"><circle cx="15" cy="15" r="13" fill="none" stroke="#f37122" stroke-width="2"/><path d="M10 8l3 0 1 4-2 1.5a9 9 0 0 0 4.5 4.5L18 16l4 1v3c-7 0-12-5-12-12z" fill="#f37122"/></svg>888-888-8888</span>
    <span><svg width="36" height="22" viewBox="0 0 36 22"><rect x="9" y="2" width="25" height="18" fill="none" stroke="#f37122" stroke-width="2"/><path d="M9 2l12.5 10L34 2" fill="none" stroke="#f37122" stroke-width="2"/><path d="M0 7h6M2 12h4M0 17h6" stroke="#f37122" stroke-width="2"/></svg>info@reidcalloway.com</span>
  </div>
  <nav class="abs main-nav">
    <a class="active" href="#">Home</a><a href="#">Experience</a><a href="#">Consulting</a><a href="#">Lectures</a><a href="#">Affiliates</a><a href="#">Media</a><a href="#">Contact</a>
  </nav>
</header>

<section class="abs hero">
  <div class="abs hero-portrait" role="img" aria-label="Portrait of the physician in a white EMS uniform shirt and sunglasses, arms crossed"></div>
  <div class="abs hero-title">REID CALLOWAY</div>
  <div class="abs hero-sub">Lorem ipsum dolor sit amet, consectetur adipiscing elit</div>
  <div class="abs btn-outline">LEARN MORE</div>
  <div class="abs play-video">
    <svg width="58" height="58" viewBox="0 0 58 58"><circle cx="29" cy="29" r="29" fill="#111"/><path d="M23 17l17 12-17 12z" fill="#fff"/></svg>
    <span>PLAY THE<br>VIDEO</span>
  </div>
  <div class="abs hero-strip">
    <div role="img" aria-label="Video still beside an ambulance" style="background:linear-gradient(135deg,#b7c93a,#3c4a3a)"></div>
    <div role="img" aria-label="Video still of a lecture room with projector" style="background:linear-gradient(135deg,#6a5a48,#2b2e4a)"></div>
    <div role="img" aria-label="Video still of a seminar audience" style="background:linear-gradient(135deg,#7a6a5c,#30303a)"></div>
  </div>
</section>

<h2 class="section-title" style="top:784px">OUR MEDIA</h2>
<div class="abs media-sub">See What's new in the production of TV shows</div>

<div class="photo" style="left:112px;top:871px;width:311px;height:212px;background:linear-gradient(160deg,#c9b58c,#6a4a2c 60%,#3a2a1c)" role="img" aria-label="Group holding awards at a community event"></div>
<div class="photo" style="left:444px;top:871px;width:311px;height:212px;background:linear-gradient(160deg,#b9c0c6,#4d5560 60%,#25303a);overflow:hidden" role="img" aria-label="Panel discussion at a wilderness care conference">
  <svg class="abs" style="left:132px;top:68px" width="50" height="50" viewBox="0 0 50 50"><circle cx="25" cy="25" r="23" fill="#fff" stroke="#a54499" stroke-width="3"/><path d="M20 14l15 11-15 11z" fill="#a54499"/></svg>
  <div class="ep-bar"><span>Alder Ridge Wilderness Care<br>Conference</span><em>(2 Episodes)</em></div>
</div>
<div class="photo" style="left:776px;top:871px;width:312px;height:212px;background:linear-gradient(160deg,#cbb8a0,#5a4636 60%,#2a221c)" role="img" aria-label="Crowded reception with balloons"></div>
<div class="photo" style="left:112px;top:1103px;width:311px;height:211px;background:linear-gradient(160deg,#e6e6e6,#3c4a3c 60%,#1f2a22)" role="img" aria-label="Two responders beside an emergency vehicle"></div>
<div class="photo" style="left:444px;top:1103px;width:311px;height:211px;background:linear-gradient(160deg,#c9a780,#7a6a58 60%,#4a3c30)" role="img" aria-label="Selfie of two colleagues"></div>
<div class="photo" style="left:776px;top:1103px;width:312px;height:211px;background:linear-gradient(160deg,#d0d2d6,#6a6c72 60%,#34363c)" role="img" aria-label="Hands-on training session with a manikin"></div>

<svg class="round-arrow" style="left:56px;top:1067px" viewBox="0 0 40 40"><circle cx="20" cy="20" r="18" fill="none" stroke="#fff" stroke-width="2.5"/><path d="M23 12l-8 8 8 8" fill="none" stroke="#fff" stroke-width="2.5"/></svg>
<svg class="round-arrow" style="left:1104px;top:1067px" viewBox="0 0 40 40"><circle cx="20" cy="20" r="18" fill="none" stroke="#fff" stroke-width="2.5"/><path d="M17 12l8 8-8 8" fill="none" stroke="#fff" stroke-width="2.5"/></svg>

<section class="abs about">
  <h3>ABOUT ME IN THE MEDIA</h3>
  <p>Reid Calloway, DO, EMT-P, FAWM, is an assistant professor of emergency medicine and EMS at Northgate State University. He's an active EMS physician with multiple departments in the region, including medical director for Coral Bay Fire Rescue Gulf Task Force Seven USAR and very active globally in wilderness/austere EMS.Specialties: International Emergency Medicine, Prehospital Care, Emergency Medicine / EMS Education,</p>
  <div class="abs btn-cv">TAKE A LOOK AT MY CV
    <svg width="14" height="14" viewBox="0 0 14 14"><circle cx="7" cy="7" r="6" fill="none" stroke="#fff" stroke-width="1.6"/><path d="M6 4.5L8.5 7 6 9.5" fill="none" stroke="#fff" stroke-width="1.6"/></svg>
  </div>
  <div class="abs" style="left:567px;top:42px;width:383px;height:263px;background:linear-gradient(150deg,#a8b2b8,#4a4a4a 55%,#1f2a3c)" role="img" aria-label="Outdoor selfie of two rescue team members in sunglasses"></div>
</section>

<h2 class="section-title" style="top:1831px">OUR&nbsp; GALLERY</h2>
<div class="g-tile" style="left:112px;top:1904px;width:230px;height:179px;background:linear-gradient(150deg,#c8a686,#5a4a3e)" role="img" aria-label="Three colleagues smiling together"></div>
<div class="g-tile" style="left:112px;top:2105px;width:230px;height:178px;background:linear-gradient(150deg,#8a8f96,#2a2e34)" role="img" aria-label="Responder in uniform and sunglasses"></div>
<div class="g-tile" style="left:361px;top:1904px;width:230px;height:179px;background:linear-gradient(150deg,#c8d0d6,#4e9a4a 60%,#3a3e44)" role="img" aria-label="Medical aircraft on the tarmac"></div>
<div class="g-tile" style="left:361px;top:2105px;width:230px;height:178px;background:linear-gradient(150deg,#6a8a8a,#2a5a6a 60%,#1a2e3a)" role="img" aria-label="Medical team transferring a patient"></div>
<div class="g-tile" style="left:609px;top:1904px;width:230px;height:179px;background:linear-gradient(150deg,#d4ccb8,#8a7a5c 60%,#4a3e30)" role="img" aria-label="Team posing with bananas in an office"></div>
<div class="g-tile" style="left:609px;top:2105px;width:230px;height:178px;background:linear-gradient(150deg,#8cb4d8,#8a6a4a 60%,#3e2e22)" role="img" aria-label="Close-up outdoor portrait in sunglasses"></div>
<div class="g-tile" style="left:858px;top:1904px;width:230px;height:379px;background:linear-gradient(170deg,#e6e2d6,#9a5a4a 40%,#2a2a2a 80%)" role="img" aria-label="Standing beside a painting with a dog on a couch"></div>
<svg class="round-arrow" style="left:56px;top:2073px" viewBox="0 0 40 40"><circle cx="20" cy="20" r="18" fill="none" stroke="#fff" stroke-width="2.5"/><path d="M23 12l-8 8 8 8" fill="none" stroke="#fff" stroke-width="2.5"/></svg>
<svg class="round-arrow" style="left:1104px;top:2073px" viewBox="0 0 40 40"><circle cx="20" cy="20" r="18" fill="none" stroke="#fff" stroke-width="2.5"/><path d="M17 12l8 8-8 8" fill="none" stroke="#fff" stroke-width="2.5"/></svg>

<h2 class="section-title" style="top:2362px">MY CONSULTING</h2>
<div class="abs" style="left:112px;top:2431px;width:488px;height:390px;background:linear-gradient(180deg,#c0c8d4 0%,#5a4a3a 50%,#2a221c 100%)" role="img" aria-label="Lecture hall with a presentation on snakebite management">
  <svg class="abs" style="left:214px;top:120px" width="60" height="60" viewBox="0 0 60 60"><circle cx="30" cy="30" r="27" fill="#fff" stroke="#a54499" stroke-width="3"/><path d="M24 17l18 13-18 13z" fill="#a54499"/></svg>
  <div class="c-bar" style="background:var(--purple)">TRAINING<svg width="30" height="30" viewBox="0 0 30 30"><circle cx="15" cy="15" r="13" fill="none" stroke="#fff" stroke-width="2"/><path d="M9 15h12M16 10l5 5-5 5" fill="none" stroke="#fff" stroke-width="2"/></svg></div>
</div>
<div class="abs" style="left:600px;top:2431px;width:488px;height:198px;background:linear-gradient(160deg,#d8dce0,#6a5a4c 55%,#2e2822)" role="img" aria-label="Speaker presenting to a seated audience">
  <div class="c-bar" style="background:var(--blue)">RESEARCH<svg width="30" height="30" viewBox="0 0 30 30"><circle cx="15" cy="15" r="13" fill="none" stroke="#fff" stroke-width="2"/><path d="M9 15h12M16 10l5 5-5 5" fill="none" stroke="#fff" stroke-width="2"/></svg></div>
</div>
<div class="abs" style="left:600px;top:2629px;width:488px;height:192px;background:linear-gradient(160deg,#6a7a8c,#3a3230 55%,#1e1a18)" role="img" aria-label="Speaker with a microphone at a podium">
  <div class="c-bar" style="background:var(--green)">TELEVISION<svg width="30" height="30" viewBox="0 0 30 30"><circle cx="15" cy="15" r="13" fill="none" stroke="#fff" stroke-width="2"/><path d="M9 15h12M16 10l5 5-5 5" fill="none" stroke="#fff" stroke-width="2"/></svg></div>
</div>
<svg class="round-arrow" style="left:56px;top:2608px" viewBox="0 0 40 40"><circle cx="20" cy="20" r="18" fill="none" stroke="#fff" stroke-width="2.5"/><path d="M23 12l-8 8 8 8" fill="none" stroke="#fff" stroke-width="2.5"/></svg>
<svg class="round-arrow" style="left:1104px;top:2608px" viewBox="0 0 40 40"><circle cx="20" cy="20" r="18" fill="none" stroke="#fff" stroke-width="2.5"/><path d="M17 12l8 8-8 8" fill="none" stroke="#fff" stroke-width="2.5"/></svg>

<h2 class="section-title" style="top:2901px">WE ARE PROUD TO WORK WITH THESE AFFILIATES</h2>
<div class="abs affiliates">
  <span><i></i>Mailgrove</span>
  <span><i></i>PLACEHOLDER</span>
  <span><i></i>placeholder</span>
  <span><i></i>voxline</span>
  <span><i></i>scriptly</span>
</div>

<section class="abs contact">
  <div class="abs contact-photo" role="img" aria-label="Physician in blue scrubs eating a banana in front of ambulances"></div>
  <h3>CONTACT US</h3>
  <div class="lead">Fill the form below &amp; get in touch with us</div>
  <div class="field" style="left:140px;top:136px;width:344px">&#128100; Full Name</div>
  <div class="field" style="left:140px;top:200px;width:344px">&#9993; Email Address</div>
  <div class="field" style="left:140px;top:263px;width:344px">&#9998; Subject</div>
  <div class="field" style="left:492px;top:136px;width:344px;height:114px">&#9679; Message</div>
  <div class="submit"><svg width="16" height="16" viewBox="0 0 16 16"><path d="M1 7l14-6-5 14-2-6z" fill="#fff"/></svg>SUBMIT</div>
</section>

<footer>
  <div class="abs footer-brand"><div class="name">REID CALLOWAY</div><div class="tag">wilderness &amp; EMS</div></div>
  <div class="abs socials" aria-label="Social links"><i></i><i></i><i></i><i></i></div>
  <div class="abs f-col" style="left:459px"><h4>QUICK LINKS</h4>Home<br>About Us<br>Media<br>Contact Us</div>
  <div class="abs f-col" style="left:688px"><h4>OUR SHOWS</h4>Interviews<br>Techings<br>Training<br>Research</div>
  <div class="abs f-col" style="left:917px"><h4>HEAD OFFICE</h4>2/F, Your Location<br>Lorem Ipsum, Ny6300<br>Email: Info@reidcalloway.com<br>Phone: +888-888-888<br><span class="dir">Get Directions</span></div>
  <div class="abs footer-rule"></div>
  <div class="abs copyright">Copyright © 2019. All Rights Reserved</div>
</footer>

</body>
</html>
```